Brenwick Structures Construction Company Seeking Modern Website

We are a small construction company wanting to create a web presence. We don't have much in the way of current content but will get photos as they come in. Attached is a picture of our business card.
The pages we would like on the menu are:
Home
Portfolio
Product Specs
Testimonials
Our Process
Contact
Some designs we like are:
http://www.tovasheds-example.com/
http://www.qrnstructures-example.com/
http://dunholtbarns-example.com/
http://pellingframes-example.com/
Not much requirements other than that so feel free to be creative!
Updates
Target Market(s)
Construction
Commercial and Residential Buildings
Industry/Entity Type
Construction Company
Number of Pages Required
5+ page
Look and feel

```html
<!DOCTYPE html>
<html lang="en">
<head>
<meta charset="utf-8">
<title>Brenwick Structures</title>
<link rel="stylesheet" href="https://fonts.googleapis.com/css2?family=Lobster&family=Open+Sans:wght@400;600&display=swap">
<style>
:root{
  --blue:#1ba4dc;
  --red:#d93a30;
  --red-deep:#b8231d;
  --ink:#2b2b2b;
  --text:#555;
  --white:#fff;
}
*{margin:0;padding:0;box-sizing:border-box}
html,body{width:758px;height:1200px;overflow:hidden;background:var(--white)}
body{position:relative;font-family:"Open Sans",sans-serif;color:var(--text)}
a{text-decoration:none}
.abs{position:absolute}
.script{font-family:"Lobster",cursive}

.topbar{left:0;top:0;width:758px;height:18px;background:var(--blue);color:var(--white);font-size:6px}
.topbar .contact{left:102px;top:5px;display:flex;gap:22px;align-items:center}
.topbar .contact span{display:flex;align-items:center;gap:8px}
.topbar .social{right:112px;top:5px;display:flex;gap:10px}
.topbar .social i{display:block;width:8px;height:8px;border-radius:50%;background:rgba(255,255,255,.85)}

.header{left:0;top:18px;width:758px;height:68px;background:var(--white)}
.brand{left:100px;top:25px;display:flex;align-items:center;gap:6px;font-family:"Lobster",cursive;font-size:19px;color:var(--blue)}
.brand i{display:block;width:10px;height:10px;background:var(--red);border-radius:50%}
.nav{left:310px;top:25px;display:flex;align-items:center;font-family:"Lobster",cursive;font-size:9.5px;color:var(--ink)}
.nav a{color:inherit;margin-right:20px}
.nav a:last-child{margin-right:0}
.nav a.active{background:var(--red);color:var(--white);border:1.5px solid #8e1a14;border-radius:12px;padding:4px 12px;margin-right:12px}

.hero{left:0;top:86px;width:758px;height:342px}
.hero-photo{left:0;top:0;width:758px;height:342px;background:linear-gradient(180deg,#6f6a62 0%,#8d8170 45%,#a08f77 70%,#7c6d5c 100%)}
.hero-title{left:0;top:112px;width:758px;text-align:center;color:var(--white);font-size:21px;font-weight:400}
.hero-sub{left:0;top:148px;width:758px;text-align:center;color:var(--white);font-size:13px;line-height:16px}
.cta{left:310px;top:200px;width:138px;height:28px;border-radius:14px;background:var(--blue);border:2px solid #0f5f86;color:var(--white);font-family:"Lobster",cursive;font-size:12px;display:flex;align-items:center}
.cta .ic{width:30px;height:30px;margin-left:-2px;border-radius:50%;background:var(--white);border:2px solid #222;display:flex;align-items:center;justify-content:center}
.cta .lbl{margin-left:10px}
.dots{left:356px;top:323px;display:flex;gap:3px}
.dots i{width:7px;height:7px;border-radius:50%;background:var(--white)}
.dots i.on{background:var(--blue)}

.h2{font-family:"Lobster",cursive;color:var(--ink);font-size:17px;font-weight:400}
.h2 em{font-style:normal;color:var(--red)}
.welcome-title{left:0;top:446px;width:758px;text-align:center;font-size:18px}
.welcome-text{left:176px;top:480px;width:406px;text-align:center;font-size:6.4px;line-height:12.3px}
.divider{left:102px;width:554px;height:3px;background:repeating-linear-gradient(90deg,#cfcfcf 0 2px,transparent 2px 4px)}

.svc-img{width:169px;height:114px;border:1px solid #ddd;padding:2px;background:var(--white)}
.svc-img div{width:100%;height:100%}
.svc-name{font-family:"Lobster",cursive;color:var(--blue);font-size:12px;font-weight:400}
.svc-text{font-size:6.4px;line-height:12.5px;width:172px}
.more-btn{width:73px;height:21px;border-radius:11px;background:var(--red);border:1.5px solid #333;color:var(--white);font-family:"Lobster",cursive;font-size:8px;display:flex;align-items:center}
.more-btn .ic{width:21px;height:21px;margin-left:-2px;border-radius:50%;background:var(--white);border:1.5px solid #333;display:flex;align-items:center;justify-content:center}
.more-btn .lbl{margin-left:9px}

.news-img{left:488px;width:54px;height:46px}
.news-text{left:553px;width:106px;font-size:6.4px;line-height:11.4px}
.news-date{left:553px;font-family:"Lobster",cursive;font-size:6.6px;color:var(--blue);display:flex;gap:5px;align-items:center}
.news-rule{left:488px;width:168px;height:1px;background:#e6e6e6}

.project{width:268px;height:107px;border:1px solid #e2e2e2;background:var(--white)}
.project .img{left:0;top:0;width:117px;height:105px}
.project .name{left:130px;top:10px;font-family:"Lobster",cursive;color:var(--blue);font-size:12px;font-weight:400}
.project .txt{left:130px;top:33px;width:128px;font-size:6.4px;line-height:11.4px}
.project .link{left:130px;top:82px;font-family:"Lobster",cursive;color:var(--red);font-size:8px;display:flex;gap:3px;align-items:center}

.footer{left:0;top:1030px;width:758px;height:170px;background:linear-gradient(180deg,#de4137 0%,#d5302a 100%);color:var(--white);font-size:6.4px}
.footer h4{font-family:"Lobster",cursive;font-weight:400;font-size:8.5px;position:absolute;top:22px}
.footer ul{list-style:none;position:absolute;top:42px;line-height:12.8px}
.footer li{display:flex;gap:7px;align-items:center}
.footer li.indent{padding-left:10px}
.news-in{left:489px;top:72px;width:167px;height:20px;border-radius:10px;background:var(--white);display:flex;align-items:center;overflow:hidden;color:#777}
.news-in .ic{width:20px;height:20px;border-radius:50%;border:1.5px solid var(--red);display:flex;align-items:center;justify-content:center;margin-right:8px}
.news-in .btn{margin-left:auto;height:20px;width:41px;background:var(--blue);color:var(--white);font-family:"Lobster",cursive;font-size:8px;display:flex;align-items:center;justify-content:center}
.copy{left:0;top:128px;width:758px;text-align:center}
.base-band{left:0;top:1190px;width:758px;height:10px;background:var(--red-deep)}
</style>
</head>
<body>

<div class="abs topbar">
  <div class="abs contact">
    <span><svg width="7" height="7" viewBox="0 0 10 10"><path d="M2 0l2 2-1 2 3 3 2-1 2 2-2 2C4 10 0 6 0 2z" fill="#fff"/></svg>Call Us:014-260-4471</span>
    <span><svg width="8" height="6" viewBox="0 0 10 7"><rect width="10" height="7" fill="#fff"/><path d="M0 0l5 4 5-4" stroke="#1ba4dc" fill="none"/></svg>Email:hello@brenwick-example.com</span>
  </div>
  <div class="abs social"><i></i><i></i><i></i><i></i><i></i></div>
</div>

<div class="abs header">
  <div class="abs brand"><i></i>Brenwick Structures</div>
  <nav class="abs nav">
    <a class="active" href="#">Home</a>
    <a href="#">Portfolio</a>
    <a href="#">Product Specs</a>
    <a href="#">Testimonials</a>
    <a href="#">Our Process</a>
    <a href="#">Contact</a>
  </nav>
</div>

<section class="abs hero">
  <div class="abs hero-photo" role="img" aria-label="City skyline with construction cranes and high-rise towers"></div>
  <svg class="abs" style="left:0;top:0" width="758" height="342" viewBox="0 0 758 342"><path d="M0 292 Q379 400 758 292 L758 342 L0 342 Z" fill="#fff"/></svg>
  <h1 class="abs hero-title script">Building Dreams, so you can Build Memories</h1>
  <p class="abs hero-sub">Sed ut perspiciatis unde omnis iste natus error sit voluptatem<br>accusantium doloremque laudantium, totam rem.</p>
  <a class="abs cta" href="#"><span class="ic"><svg width="10" height="10" viewBox="0 0 10 10"><path d="M1 9l1-3 5-5 2 2-5 5z" fill="#1ba4dc"/></svg></span><span class="lbl">Get Started Here</span></a>
  <div class="abs dots"><i></i><i></i><i class="on"></i><i></i><i></i></div>
</section>

<h2 class="abs h2 welcome-title">Welcome to <em>Brenwick Structures</em></h2>
<p class="abs welcome-text">Sed ut perspiciatis unde omnis iste natus error sit voluptatem accusantium doloremque laudantium, totam rem aperiam, eaque ipsa quae ab illo inventore veritatis et quasi architecto beatae vitae dicta sunt explicabo. Nemo enim ipsam voluptatem quia voluptasSed ut perspiciatis unde omnis iste natus error sit voluptatem accusantium doloremque laudantium, totam rem aperiam, eaque ipsa quae ab illo inventore veritatis et quasi architecto beatae vitae dicta sunt explicabo. Nemo enim ipsam voluptatem .</p>
<div class="abs divider" style="top:550px"></div>

<h2 class="abs h2" style="left:100px;top:563px">Our <em>Services</em></h2>
<div class="abs svc-img" style="left:102px;top:600px"><div role="img" aria-label="Commercial construction site with cranes at dusk" style="background:linear-gradient(180deg,#3b4f86 0%,#6a6078 45%,#b08448 100%)"></div></div>
<div class="abs svc-img" style="left:290px;top:600px"><div role="img" aria-label="Modern residential apartment building with gardens" style="background:linear-gradient(180deg,#8fb9e0 0%,#c9a888 50%,#6f9a4a 100%)"></div></div>
<h3 class="abs svc-name" style="left:102px;top:721px">Commercial Construction</h3>
<h3 class="abs svc-name" style="left:290px;top:721px">Residential Buildings</h3>
<p class="abs svc-text" style="left:102px;top:742px">Sed ut perspiciatis unde omnis iste natus error sitvoluj up tatem accusantium doloremque laudantium, totam rem aperiam, eaque ipsa quae ab illoinventor.</p>
<p class="abs svc-text" style="left:290px;top:742px">Sed ut perspiciatis unde omnis iste natus error sitvoluj up tatem accusantium doloremque laudantium, totam rem aperiam, eaque ipsa quae ab illoinventor.</p>
<a class="abs more-btn" href="#" style="left:102px;top:788px"><span class="ic"><svg width="9" height="9" viewBox="0 0 10 10"><circle cx="5" cy="5" r="4.2" fill="none" stroke="#d93a30" stroke-width="1.4"/><path d="M4 3l2 2-2 2" stroke="#d93a30" fill="none" stroke-width="1.4"/></svg></span><span class="lbl">Read More</span></a>
<a class="abs more-btn" href="#" style="left:290px;top:788px"><span class="ic"><svg width="9" height="9" viewBox="0 0 10 10"><circle cx="5" cy="5" r="4.2" fill="none" stroke="#d93a30" stroke-width="1.4"/><path d="M4 3l2 2-2 2" stroke="#d93a30" fill="none" stroke-width="1.4"/></svg></span><span class="lbl">Read More</span></a>

<h2 class="abs h2" style="left:487px;top:563px">Our <em>News</em></h2>
<div class="abs news-img" style="top:600px;background:linear-gradient(160deg,#e7a05c,#8b4f5a)" role="img" aria-label="Business partners shaking hands at sunset"></div>
<p class="abs news-text" style="top:597px">Sed ut perspilciatis unde omniste natus error sitvojul upnatus error sitvojul uptatemlautatemlaud.</p>
<div class="abs news-date" style="top:635px"><svg width="7" height="7" viewBox="0 0 10 10"><rect x="0.5" y="1.5" width="9" height="8" fill="none" stroke="#1ba4dc"/><path d="M0.5 4h9" stroke="#1ba4dc"/></svg>Nov 19 2015</div>
<div class="abs news-rule" style="top:659px"></div>
<div class="abs news-img" style="top:670px;background:linear-gradient(180deg,#8a7aa8,#b08a70 60%,#5e8a3e)" role="img" aria-label="Suburban family house"></div>
<p class="abs news-text" style="top:668px">Sed ut perspilciatis unde omniste natus error sitvojul upnatus error sitvojul uptatemlautatemlaud.</p>
<div class="abs news-date" style="top:706px"><svg width="7" height="7" viewBox="0 0 10 10"><rect x="0.5" y="1.5" width="9" height="8" fill="none" stroke="#1ba4dc"/><path d="M0.5 4h9" stroke="#1ba4dc"/></svg>Nov 19 2015</div>
<div class="abs news-rule" style="top:730px"></div>
<div class="abs news-img" style="top:748px;background:linear-gradient(160deg,#d9b35a,#8a6c50 60%,#4d5f70)" role="img" aria-label="Construction workers in hard hats on site"></div>
<p class="abs news-text" style="top:745px">Sed ut perspilciatis unde omniste natus error sitvojul upnatus error sitvojul uptatemlautatemlaud.</p>
<div class="abs news-date" style="top:784px"><svg width="7" height="7" viewBox="0 0 10 10"><rect x="0.5" y="1.5" width="9" height="8" fill="none" stroke="#1ba4dc"/><path d="M0.5 4h9" stroke="#1ba4dc"/></svg>Nov 19 2015</div>
<div class="abs news-rule" style="top:807px"></div>

<div class="abs divider" style="top:849px"></div>

<h2 class="abs h2" style="left:102px;top:861px">Our <em>Projects</em></h2>
<article class="abs project" style="left:102px;top:899px">
  <div class="abs img" role="img" aria-label="Glass office building with trees and a plaza" style="background:linear-gradient(180deg,#5c8a6a 0%,#7aa04e 50%,#bfc2b8 100%)"></div>
  <h3 class="abs name">Project Name</h3>
  <p class="abs txt">Sed ut perspiciatis unde omnis e natusor situptatem accusantium doloremque laudatium, totrem aperiam, eaque ipsa quaetuptatem accusantium dolor.</p>
  <a class="abs link" href="#">Read More <svg width="7" height="7" viewBox="0 0 10 10"><circle cx="5" cy="5" r="4.2" fill="none" stroke="#d93a30" stroke-width="1.4"/><path d="M4 3l2 2-2 2" stroke="#d93a30" fill="none" stroke-width="1.4"/></svg></a>
</article>
<article class="abs project" style="left:388px;top:899px">
  <div class="abs img" role="img" aria-label="Modern office tower at twilight" style="background:linear-gradient(180deg,#3a4a66 0%,#6f7a88 55%,#2e3540 100%)"></div>
  <h3 class="abs name">Project Name</h3>
  <p class="abs txt">Sed ut perspiciatis unde omnis e natusor situptatem accusantium doloremque laudatium, totrem aperiam, eaque ipsa quaetuptatem accusantium dolor.</p>
  <a class="abs link" href="#">Read More <svg width="7" height="7" viewBox="0 0 10 10"><circle cx="5" cy="5" r="4.2" fill="none" stroke="#d93a30" stroke-width="1.4"/><path d="M4 3l2 2-2 2" stroke="#d93a30" fill="none" stroke-width="1.4"/></svg></a>
</article>

<footer class="abs footer">
  <h4 style="left:102px">Contact Us</h4>
  <ul style="left:102px">
    <li><svg width="6" height="7" viewBox="0 0 6 8"><path d="M3 0a3 3 0 013 3c0 2-3 5-3 5S0 5 0 3a3 3 0 013-3z" fill="#fff"/></svg>2870 Larkmoor Rd.</li>
    <li class="indent">Hollin Vale, KS 66390</li>
    <li><svg width="6" height="6" viewBox="0 0 10 10"><path d="M2 0l2 2-1 2 3 3 2-1 2 2-2 2C4 10 0 6 0 2z" fill="#fff"/></svg>Commercial: (620)555-0142</li>
    <li><svg width="6" height="6" viewBox="0 0 10 10"><rect y="3" width="10" height="6" fill="#fff"/><rect x="2" width="6" height="4" fill="#fff"/></svg>Fax: (620)555-0187</li>
    <li><svg width="6" height="5" viewBox="0 0 10 7"><rect width="10" height="7" fill="#fff"/></svg>Email:hello@brenwick-example.com</li>
  </ul>
  <h4 style="left:249px">Services</h4>
  <ul style="left:249px">
    <li>»&nbsp; Commercial Construction</li>
    <li>»&nbsp; Residential Buildings</li>
    <li>»&nbsp; Other Services</li>
  </ul>
  <h4 style="left:379px">Quick Links</h4>
  <ul style="left:379px">
    <li>»&nbsp; Available Property</li>
    <li>»&nbsp; Property Showcase</li>
    <li>»&nbsp; Commercial Services</li>
    <li>»&nbsp; Work Order</li>
  </ul>
  <h4 style="left:494px">Newsletter</h4>
  <p class="abs" style="left:494px;top:42px;width:170px;line-height:10.5px">Lorem ipsum dolor lorem sit amet, consectetuer adip iscing elit, sdolor sit ametce.</p>
  <div class="abs news-in"><span class="ic"><svg width="8" height="6" viewBox="0 0 10 7"><rect width="10" height="7" fill="#d93a30"/><path d="M0 0l5 4 5-4" stroke="#fff" fill="none"/></svg></span>Email Adrress:<span class="btn">SignUp</span></div>
  <p class="abs copy">Copyright © 2015 Brenwick Structures| Sitemap . Privacy Policy</p>
</footer>
<div class="abs base-band"></div>

</body>
</html>
```